Chicago Train Advertisement for RideNestHomes.com.

We have purchased one month of advertising on the Chicago RLX subway train. We will have 150 cards up in the subway to advertise our website RideNestHomes.com where people can search for properties by train station. The cards are 11" tall and 46.5" long. We want people to feel compelled to jump on their cell phones and conduct a search for an apartment or home while they are riding the train, or at least enter their email and search criteria so one of our agents can help them.

Target Market(s)

People who want to live near train stations

Industry/Entity Type

Real Estate

Font styles to use
Sans Serif

Colors

Designer to choose colors to be used in the design.

Requirements
Must have
• The ridenesthomes logo and a catchy slogan, something like: Find your home near a train station the easy way: www.ridenesthome.com. Search real estate listings near the RLX or Valox.

```html
<!DOCTYPE html>
<html lang="en">
<head>
<meta charset="utf-8">
<title>RideNestHomes.com – Train Card</title>
<link rel="stylesheet" href="https://fonts.googleapis.com/css2?family=Montserrat:wght@500;700&display=swap">
<style>
  :root {
    --page-bg: #e9ebee;
    --navy-deep: #0a1f6b;
    --blue-mid: #0d4f96;
    --blue-bright: #1467b0;
    --photo-sky: #4a7fd0;
    --photo-tower: #1c2f6e;
    --white: #ffffff;
    --rule: rgba(255, 255, 255, 0.75);
  }
  * { box-sizing: border-box; margin: 0; padding: 0; }
  html, body {
    width: 1200px;
    height: 865px;
    overflow: hidden;
    background: var(--page-bg);
  }
  .transit-card {
    position: absolute;
    left: 40px;
    top: 300px;
    width: 1120px;
    height: 265px;
    background: linear-gradient(90deg, var(--blue-bright) 0%, var(--blue-mid) 45%, var(--navy-deep) 100%);
    overflow: hidden;
    font-family: "Montserrat", sans-serif;
    color: var(--white);
  }
  .skyline-photo {
    position: absolute;
    left: 0;
    top: 0;
    width: 440px;
    height: 100%;
    background: radial-gradient(circle at 55% 40%, var(--photo-sky) 0%, #3560a8 35%, var(--photo-tower) 100%);
    clip-path: polygon(0 0, 82% 0, 100% 42%, 76% 100%, 0 100%);
  }
  .brand-block {
    position: absolute;
    right: 70px;
    top: 38px;
    width: 560px;
    display: flex;
    flex-direction: column;
    align-items: flex-end;
  }
  .brand-logo {
    display: flex;
    align-items: center;
    gap: 14px;
    font-weight: 500;
    font-size: 44px;
    letter-spacing: -0.5px;
  }
  .brand-logo-dot {
    width: 22px;
    height: 22px;
    border-radius: 50%;
    background: var(--white);
  }
  .brand-rule {
    width: 100%;
    height: 2px;
    margin: 18px 0 20px;
    background: linear-gradient(90deg, transparent 0%, var(--rule) 25%, var(--rule) 100%);
  }
  .headline {
    text-align: right;
    font-weight: 700;
    font-size: 40px;
    line-height: 1.15;
    text-transform: uppercase;
    letter-spacing: 0.5px;
  }
</style>
</head>
<body>
  <section class="transit-card">
    <div class="skyline-photo" role="img" aria-label="Photo looking straight up at Chicago skyscrapers against a blue sky"></div>
    <div class="brand-block">
      <div class="brand-logo">
        <span class="brand-logo-dot"></span>
        <span class="brand-logo-name">RideNestHomes.com</span>
      </div>
      <div class="brand-rule"></div>
      <h1 class="headline">Find Chicagoland<br>Homes Near Transit</h1>
    </div>
  </section>
</body>
</html>
```